Exciting new aperitif brand needs a great label

Vel-Orin is a wonderful rich new premium-priced bitter aperitif, with a deep red colour, from a 100+ year old distillery (1890) near Turin in the Piedmont region of Italy. Inspired by Tessoni, it is perfectly formulated to elevate the classic Bravetti cocktail (and variations on it). It also goes perfectly in a Spritz or a long mixed drink with soda or tonic. The name Vel-Orin is derived from the French for 'peak' and the Italian word for 'love'.

The label, which should take inspiration from Tessoni, but be distinctively different, can incoporate any number of premium label embellishments (foil, embossing, textures etc) and should be no greater than 11cm (height) x 9cm (width) with any core imagery restricted to a width of c.7cm.

The attached mood board should act as inspiration and colour should largely be restricted to reds, blues, whites and perhaps orange. For completeness, the label should note that the ABV is 25% and the bottle size 70cl.

Target Market(s)

21-45yr olds - equal split female/male

Colors
0054AA
0677BA
7BADD7
CADEEF
E8F1F8
0094D4
00A9DD
6FCCEA
C7EBF8
E9F6FB
EE7325
F08F49
F5BC92
FAE3D3
FDF4ED
EB3D1F
EC4F4E
F09395
F8D3D4
FCEDEE

Requirements
Must have
• Great lettering design on the name Vel-Orin

```html
<!DOCTYPE html>
<html lang="en">
<head>
<meta charset="utf-8">
<title>Vel-Orin Bitter Aperitivo Label</title>
<link rel="stylesheet" href="https://fonts.googleapis.com/css2?family=Alfa+Slab+One&family=Yellowtail&family=Libre+Baskerville&display=swap">
<style>
  :root {
    --backdrop: #ececec;
    --label-top: #e9f6fb;
    --label-bottom: #e8f1f8;
    --frame: #ee7325;
    --frame-light: #f5bc92;
    --ribbon: #f08f49;
    --ribbon-deep: #ee7325;
    --ribbon-ink: #fdf4ed;
    --name-blue: #0054aa;
    --ink-blue: #0677ba;
    --script-orange: #ee7325;
    --skyline-a: #c7ebf8;
    --skyline-b: #7badd7;
    --detail-red: #eb3d1f;
  }
  * { margin: 0; padding: 0; box-sizing: border-box; }
  html, body {
    width: 675px;
    height: 1200px;
    overflow: hidden;
    background: var(--backdrop);
  }
  .canvas {
    position: relative;
    width: 675px;
    height: 1200px;
    display: flex;
    align-items: center;
    justify-content: center;
  }
  .label {
    position: relative;
    width: 540px;
    height: 820px;
    border: 7px solid var(--frame);
    border-radius: 50% 50% 18px 18px / 27% 27% 18px 18px;
    background: linear-gradient(180deg, var(--label-top), var(--label-bottom));
    box-shadow: inset 0 0 0 2px var(--frame-light);
    overflow: hidden;
  }
  .ribbon {
    position: absolute;
    top: 60px;
    left: 20px;
    width: 486px;
    height: 180px;
  }
  .ribbon-text {
    font-family: "Libre Baskerville", serif;
    font-size: 17px;
    letter-spacing: 3px;
    fill: var(--ribbon-ink);
  }
  .since {
    position: absolute;
    top: 205px;
    left: 0;
    width: 100%;
    display: flex;
    align-items: center;
    justify-content: center;
    gap: 14px;
    font-family: "Libre Baskerville", serif;
    font-size: 20px;
    color: var(--ink-blue);
  }
  .since-rule {
    width: 48px;
    border-top: 2px solid var(--ink-blue);
    opacity: 0.6;
  }
  .brand-name {
    position: absolute;
    top: 300px;
    left: 0;
    width: 100%;
    text-align: center;
    font-family: "Alfa Slab One", serif;
    font-weight: 400;
    font-size: 78px;
    line-height: 1;
    letter-spacing: 1px;
    color: var(--name-blue);
    transform: scaleY(1.25);
  }
  .region {
    position: absolute;
    top: 440px;
    left: 0;
    width: 100%;
    text-align: center;
    font-family: "Yellowtail", cursive;
    font-size: 72px;
    line-height: 1.2;
    color: var(--script-orange);
    transform: rotate(-8deg);
  }
  .skyline {
    position: absolute;
    left: 0;
    bottom: 0;
    width: 100%;
    height: 250px;
    background: linear-gradient(180deg, rgba(199,235,248,0) 0%, var(--skyline-a) 55%, var(--skyline-b) 100%);
    opacity: 0.75;
  }
  .specs {
    position: absolute;
    left: 0;
    bottom: 26px;
    width: 100%;
    display: flex;
    justify-content: center;
    gap: 28px;
    font-family: "Libre Baskerville", serif;
    font-size: 20px;
    letter-spacing: 1px;
    color: var(--name-blue);
  }
  .specs-dot {
    width: 8px;
    height: 8px;
    margin-top: 8px;
    border-radius: 50%;
    background: var(--detail-red);
  }
</style>
</head>
<body>
  <main class="canvas">
    <section class="label">
      <svg class="ribbon" viewBox="0 0 486 180" aria-hidden="true">
        <defs>
          <path id="ribbon-arc" d="M 30 168 Q 243 18 456 168"/>
        </defs>
        <path d="M 20 150 Q 243 -10 466 150 L 446 178 Q 243 30 40 178 Z" fill="var(--ribbon)"/>
        <path d="M 20 150 L 0 172 L 34 174 Z" fill="var(--ribbon-deep)"/>
        <path d="M 466 150 L 486 172 L 452 174 Z" fill="var(--ribbon-deep)"/>
        <text class="ribbon-text"><textPath href="#ribbon-arc" startOffset="50%" text-anchor="middle">BITTER APERITIVO</textPath></text>
      </svg>
      <div class="since"><span class="since-rule"></span>SINCE 1890<span class="since-rule"></span></div>
      <h1 class="brand-name">VEL·ORIN</h1>
      <p class="region">Piedmont</p>
      <div class="skyline" role="img" aria-label="Faint skyline illustration of Turin landmarks"></div>
      <p class="specs"><span>25% ABV</span><span class="specs-dot"></span><span>70cl</span></p>
    </section>
  </main>
</body>
</html>
```